Industry / Entity Type

Financial consultancy / advisers

Current site is: http://www.brightmoor-counsel.com

Looking for a complete overhaul of this site, we are after a clean modern look. Will require the ability to easily add, update and remove content, hence the WordPress design.
Example:
Add case studies
Industry documentation (downloadable brochures / flyers and such)

What we like from our current site is the colour the fonts and the logo (the city of London) we would like to have other city outlines (NYC and Tokyo, Hong Kong, Singapore).

The site will be used by our potential clients to get in contact and re-view the case studies, if possible would like to have a client login area where they can download our documents like NDA’s etc and T&C’s.

Task Outline

Create a Web Design (Coded - Design and coding required)
Designer must provide full implementation/coding depending on the platform chosen by the client (i.e. WordPress theme, HTML/CSS, bootstrap etc.)

Task Description

I need a full website built that must work on desktop and mobile. I can provide the London city skyline and the font file, which we have used. Some stock industrial photos will be required.

Requirements:

*Splash page
*What We Do
*How We do it
*Who Are We? To have the same information and links as the current site
*Why use us?
*Clients: To have the same information and links as the current site
*Partners: To have the same information and links as the current site
*Contact:

Target Market(s)

Financial institutions trading Equities, Futures, Options, Forex and Fixed Income.
Regulators, Exchanges, ECN’s
Buy side firms and Sell side firms

Industry/Entity Type

Financial

Coding

Coded - Design and coding required

Number of Pages Required

5+ page

Font styles to use
Sans Serif

Colors
f04a50

Requirements
Must have
• Splash page
• What We Do
• How We do it
• Who Are We? To have the same information and links as the current site
• Why use us?
• Clients: To have the same information and links as the current site
• Partners: To have the same information and links as the current site
• Contact:

```html
<!DOCTYPE html>
<html lang="en">
<head>
<meta charset="utf-8">
<title>Brightmoor Counsel</title>
<link rel="stylesheet" href="https://fonts.googleapis.com/css2?family=Arimo:wght@400;700&family=Open+Sans:wght@600;700&display=swap">
<style>
:root{
  --red:#f04a50;
  --white:#ffffff;
  --ink:#333333;
  --muted:#555555;
  --band:#ececec;
  --footer:#ededed;
  --base:#f5f5f5;
  --field:#ffffff;
}
*{margin:0;padding:0;box-sizing:border-box}
html,body{width:1200px;height:2390px;overflow:hidden}
body{position:relative;background:var(--white);font-family:"Arimo",Arial,sans-serif;color:var(--ink)}

/* nav */
.topnav{position:absolute;left:0;top:0;width:1200px;height:48px;background:var(--red);display:flex;align-items:center;padding-left:142px}
.topnav a{font-variant:small-caps;color:var(--white);text-decoration:none;font-size:16px;letter-spacing:.6px;height:48px;line-height:48px;padding:0 18px;margin-right:9px}
.topnav a.active{background:var(--white);color:var(--red)}

/* hero */
.hero{position:absolute;left:0;top:48px;width:1200px;height:523px;background:linear-gradient(180deg,#aebdcb 0%,#8e9fb0 45%,#6d7b86 70%,#4f5960 100%)}
.hero-brand{position:absolute;left:0;width:1200px;top:92px;text-align:center;color:var(--white);font-size:22px;letter-spacing:4px;font-variant:small-caps}
.hero-brand span{display:inline-block;width:14px;height:14px;background:var(--white);margin-right:10px;vertical-align:middle}
.hero-title{position:absolute;left:0;width:1200px;top:228px;text-align:center;color:var(--white);font-size:32px;font-weight:700;letter-spacing:3px;font-variant:small-caps}
.hero-sub{position:absolute;left:0;width:1200px;top:275px;text-align:center;color:var(--white);font-family:"Open Sans",Arial,sans-serif;font-weight:700;font-size:23px}
.hero-btn{position:absolute;left:521px;top:327px;width:156px;height:39px;background:var(--red);color:var(--white);font-size:17px;font-variant:small-caps;text-align:center;line-height:39px;letter-spacing:.5px}
.arrow-box{position:absolute;width:29px;height:29px;background:var(--white);display:flex;align-items:center;justify-content:center}
.social{position:absolute;left:1171px;top:215px;width:29px}
.social div{width:29px;height:29px;display:flex;align-items:center;justify-content:center}

/* welcome */
.welcome-title{position:absolute;left:0;width:1200px;top:612px;text-align:center;color:var(--red);font-size:19px;font-weight:700;letter-spacing:1.5px;font-variant:small-caps}
.welcome-text{position:absolute;left:167px;width:866px;top:656px;text-align:center;color:var(--muted);font-size:14.5px;line-height:20.3px;letter-spacing:.9px;font-variant:small-caps}

/* features */
.feature{position:absolute;top:803px;width:295px;height:270px;text-align:center}
.feature.hl{background:var(--red);color:var(--white)}
.feature svg{position:absolute;left:128px;top:32px}
.feature h3{position:absolute;top:90px;width:100%;font-size:16px;letter-spacing:1.5px;font-variant:small-caps;font-weight:700}
.feature p{position:absolute;top:131px;left:20px;width:255px;font-size:11.5px;line-height:20.5px;letter-spacing:.8px;font-variant:small-caps;color:var(--muted)}
.feature.hl p{color:var(--white)}

/* clients */
.clients{position:absolute;left:0;top:1135px;width:1200px;height:328px;background:var(--band)}
.clients h2{position:absolute;left:133px;top:84px;color:var(--red);font-size:21px;letter-spacing:1.5px;font-variant:small-caps}
.clients p{position:absolute;left:137px;top:126px;width:168px;font-size:12.5px;line-height:21px;letter-spacing:.6px;font-variant:small-caps;color:var(--muted)}
.more-btn{position:absolute;left:137px;top:209px;width:91px;height:31px;background:var(--white);color:var(--red);font-weight:700;font-size:14px;font-variant:small-caps;text-align:center;line-height:31px;letter-spacing:1px}
.client-name{position:absolute;transform:translateX(-50%);display:flex;align-items:center;gap:8px;font-size:22px;color:#3a3a3a;white-space:nowrap}
.client-name i{display:inline-block;width:16px;height:16px;background:#3a3a3a}

/* team */
.team-title{position:absolute;left:0;width:1200px;top:1498px;text-align:center;color:var(--red);font-size:19px;font-weight:700;letter-spacing:1.5px;font-variant:small-caps}
.member{position:absolute;top:1549px;width:194px;height:257px;text-align:center}
.member .photo{position:absolute;left:0;top:0;width:194px;height:206px}
.member.hl{background:var(--red);border:3px solid var(--red)}
.member.hl .photo{left:0;top:0;width:188px;height:203px}
.member .name{position:absolute;left:0;width:100%;top:220px;color:var(--red);font-size:14px;font-weight:700;letter-spacing:1.2px;font-variant:small-caps}
.member.hl .name{color:var(--white);top:217px}
.details-btn{position:absolute;left:29px;top:105px;width:128px;height:30px;background:var(--white);color:var(--red);font-size:12px;font-weight:700;font-variant:small-caps;line-height:30px;letter-spacing:1px}

/* partners */
.partners{position:absolute;left:0;top:1833px;width:1200px;height:155px;background:var(--red)}
.partner{position:absolute;top:61px;width:196px;height:75px;background:var(--white);display:flex;align-items:center;justify-content:center;gap:8px;font-size:19px;font-weight:700;color:#2f2f2f}
.partner i{display:inline-block;width:14px;height:14px;background:#2f2f2f}

/* footer */
.footer{position:absolute;left:0;top:1988px;width:1200px;height:276px;background:var(--footer)}
.fcol{position:absolute;top:40px}
.fcol h4{font-size:17px;font-weight:400;color:#222;letter-spacing:.3px;margin-bottom:14px}
.links li{list-style:none;font-size:12px;font-variant:small-caps;letter-spacing:.6px;line-height:20.6px;color:#222;display:flex;align-items:center}
.links li::before{content:"";width:5px;height:5px;border-right:1.5px solid #222;border-top:1.5px solid #222;transform:rotate(45deg);margin:0 12px 0 4px}
.contact-row{display:flex;gap:12px;font-size:12px;font-variant:small-caps;letter-spacing:.5px;line-height:20.5px;color:#222;margin-bottom:12px}
.contact-row svg{flex:none;margin-top:4px}
.field{width:171px;height:27px;background:var(--field);border:1px solid #e2e2e2;font-size:10px;padding:7px 10px;color:#333;margin-bottom:8px}
.field.tall{height:54px}
.submit{width:109px;height:33px;background:var(--red);color:var(--white);font-size:12px;font-variant:small-caps;line-height:33px;padding-left:33px;letter-spacing:.6px;margin-top:6px}
.about p{width:204px;font-size:10px;line-height:16.4px;letter-spacing:.5px;font-variant:small-caps;color:#222;text-align:justify}

/* base */
.base{position:absolute;left:0;top:2264px;width:1200px;height:126px;background:var(--base)}
.base-brand{position:absolute;left:0;width:1200px;top:28px;text-align:center;color:#333;font-size:15px;letter-spacing:3px;font-variant:small-caps}
.base-brand span{display:inline-block;width:10px;height:10px;background:#333;margin-right:8px;vertical-align:middle}
.copy{position:absolute;left:0;width:1200px;top:96px;text-align:center;font-size:12px;letter-spacing:.6px;font-variant:small-caps;color:#222}
</style>
</head>
<body>

<nav class="topnav">
  <a class="active">Home</a><a>What we do</a><a>How we do it</a><a>Who are we</a><a>Why use us</a><a>Clients</a><a>Partners</a><a>Contact</a>
</nav>

<section class="hero" role="img" aria-label="Harbour city skyline photograph with a red-sailed junk boat on the water">
  <div class="hero-brand"><span></span>Brightmoor Counsel</div>
  <div class="hero-title">Interim Management</div>
  <div class="hero-sub">For Funds, Brokers, Vendors and IT Service Providers</div>
  <div class="hero-btn">Learn More</div>
  <div class="arrow-box" style="left:99px;top:255px"><svg width="10" height="14" viewBox="0 0 10 14"><path d="M7 2 2 7l5 5" fill="none" stroke="#f04a50" stroke-width="2"/></svg></div>
  <div class="arrow-box" style="left:1070px;top:255px"><svg width="10" height="14" viewBox="0 0 10 14"><path d="M3 2l5 5-5 5" fill="none" stroke="#f04a50" stroke-width="2"/></svg></div>
</section>

<div class="social">
  <div style="background:#1f3c6e"><svg width="10" height="10"><circle cx="5" cy="5" r="4" fill="#fff"/></svg></div>
  <div style="background:#1d9fd1"><svg width="10" height="10"><circle cx="5" cy="5" r="4" fill="#fff"/></svg></div>
  <div style="background:#d9304a"><svg width="10" height="10"><circle cx="5" cy="5" r="4" fill="#fff"/></svg></div>
  <div style="background:#5a5a5a"><svg width="13" height="10" viewBox="0 0 13 10"><rect x=".5" y=".5" width="12" height="9" fill="none" stroke="#fff"/><path d="M.5.5l6 5 6-5" fill="none" stroke="#fff"/></svg></div>
  <div style="background:#1aa0c4"><svg width="10" height="10"><circle cx="5" cy="5" r="4" fill="#fff"/></svg></div>
</div>

<h1 class="welcome-title">Welcome To Brightmoor Counsel</h1>
<p class="welcome-text">Since founding Brightmoor Counsel in 2014 we have dedicated ourselves to the provision of services. What differentiates us from other advisers or consultancies is a genuine motivation to see our clients succeed. Today's technology allows our clients to take their knowledge to the market in ways that previous generations could only dream of. That's why BMC is dedicated to seeing you choose the right technology strategy, ensuring you maintain a competitive edge over your peers.</p>

<div class="feature" style="left:132px">
  <svg width="38" height="38" viewBox="0 0 38 38"><path d="M4 17h7v17H4zM11 18l7-9 2-7c3 0 4 3 3 7l-1 5h10c2 0 3 2 2 4l-3 13c-1 2-2 3-4 3H11" fill="none" stroke="#444" stroke-width="2.2" stroke-linejoin="round"/></svg>
  <h3>What we do</h3>
  <p>Lorem ipsum dolor sit amet, consectetur adipiscing elit, sed do eiusmod tempor incididunt ut labore et dolore magna aliqua. Ut enim ad minim...</p>
</div>
<div class="feature hl" style="left:453px">
  <svg width="38" height="38" viewBox="0 0 38 38"><circle cx="19" cy="19" r="16" fill="none" stroke="#fff" stroke-width="3"/><path d="M14 15c0-3 2-5 5-5s5 2 5 4.5c0 4-5 4-5 8" fill="none" stroke="#fff" stroke-width="3"/><circle cx="19" cy="27.5" r="2" fill="#fff"/></svg>
  <h3>How we do it</h3>
  <p>Lorem ipsum dolor sit amet, consectetur adipiscing elit, sed do eiusmod tempor incididunt ut labore et dolore magna aliqua. Ut enim ad minim...</p>
</div>
<div class="feature" style="left:762px">
  <svg width="40" height="38" viewBox="0 0 40 38"><circle cx="20" cy="11" r="6" fill="#444"/><path d="M10 32c0-8 4-12 10-12s10 4 10 12z" fill="#444"/><circle cx="8" cy="14" r="4.5" fill="#444"/><path d="M0 30c0-6 3-9 8-9 2 0 3 .5 4 1-2 2-3 5-3 8z" fill="#444"/><circle cx="32" cy="14" r="4.5" fill="#444"/><path d="M40 30c0-6-3-9-8-9-2 0-3 .5-4 1 2 2 3 5 3 8z" fill="#444"/></svg>
  <h3>Who are we</h3>
  <p>Lorem ipsum dolor sit amet, consectetur adipiscing elit, sed do eiusmod tempor incididunt ut labore et dolore magna aliqua. Ut enim ad minim...</p>
</div>

<section class="clients">
  <h2>Our Clients</h2>
  <p>You will find an impressive list of clients that BMC have worked with.</p>
  <div class="more-btn">More</div>
  <div class="client-name" style="left:473px;top:84px">Northgate Labs</div>
  <div class="client-name" style="left:679px;top:84px">Tradeweave</div>
  <div class="client-name" style="left:904px;top:84px"><i></i>Corelith Data</div>
  <div class="client-name" style="left:473px;top:199px">Cellwave</div>
  <div class="client-name" style="left:679px;top:199px"><i style="border-radius:50%"></i>Quayline Tech</div>
  <div class="client-name" style="left:904px;top:199px">Vaulton</div>
</section>

<h2 class="team-title">Our Team</h2>
<div class="member hl" style="left:142px">
  <div class="photo" role="img" aria-label="Portrait photograph of Mark Ellison" style="background:linear-gradient(180deg,#b8b2a8,#8f8b86)"></div>
  <div class="details-btn">More Details</div>
  <div class="name">Mark Ellison</div>
</div>
<div class="member" style="left:381px">
  <div class="photo" role="img" aria-label="Portrait photograph of Daniel Hartley" style="background:linear-gradient(180deg,#d6cfc4,#8e7d6c)"></div>
  <div class="name">Daniel Hartley</div>
</div>
<div class="member" style="left:622px">
  <div class="photo" role="img" aria-label="Portrait photograph of Peter Ashdown" style="background:linear-gradient(180deg,#6fb8a6,#3f6f7a)"></div>
  <div class="name">Peter Ashdown</div>
</div>
<div class="member" style="left:864px">
  <div class="photo" role="img" aria-label="Black and white portrait photograph of Alice Marlow" style="background:linear-gradient(180deg,#8a8a8a,#3a3a3a)"></div>
  <div class="name">Alice Marlow</div>
</div>

<section class="partners">
  <div class="arrow-box" style="left:123px;top:81px"><svg width="10" height="14" viewBox="0 0 10 14"><path d="M7 2 2 7l5 5" fill="none" stroke="#f04a50" stroke-width="2"/></svg></div>
  <div class="partner" style="left:179px"><i style="border-radius:50%"></i>Fernhollow Net</div>
  <div class="partner" style="left:394px">Tradeweave</div>
  <div class="partner" style="left:609px">Clearpath Group</div>
  <div class="partner" style="left:824px"><i></i>Stratanet</div>
  <div class="arrow-box" style="left:1049px;top:81px"><svg width="10" height="14" viewBox="0 0 10 14"><path d="M3 2l5 5-5 5" fill="none" stroke="#f04a50" stroke-width="2"/></svg></div>
</section>

<footer class="footer">
  <div class="fcol" style="left:143px">
    <h4>QUICK LINKS</h4>
    <ul class="links"><li>Home</li><li>What we do</li><li>How we do it</li><li>Who are we</li><li>Why Use Us</li><li>Clients</li><li>Partners</li><li>Contact Us</li></ul>
  </div>
  <div class="fcol" style="left:392px">
    <h4>CONTACT US</h4>
    <div class="contact-row"><svg width="11" height="14" viewBox="0 0 11 14"><path d="M5.5 0C2.5 0 0 2.4 0 5.3 0 9 5.5 14 5.5 14S11 9 11 5.3C11 2.4 8.5 0 5.5 0z" fill="#222"/><circle cx="5.5" cy="5.3" r="2" fill="#ededed"/></svg><div>Suite 4 Harlow Court,<br>Fenwick, Ashbury,<br>Wessex, AB12 3CD</div></div>
    <div class="contact-row"><svg width="12" height="12" viewBox="0 0 12 12"><path d="M2.5 0 4.5 3 3 4.5c.8 1.8 2.5 3.6 4.5 4.5L9 7.5l3 2-1.5 2.5C5 12 0 7 0 1.5z" fill="#222"/></svg><div>+44(0)20 7946 0182.</div></div>
    <div class="contact-row"><svg width="12" height="9" viewBox="0 0 12 9"><rect width="12" height="9" fill="#222"/><path d="M0 0l6 5 6-5" fill="none" stroke="#ededed"/></svg><div>admin@brightmoor-counsel.com</div></div>
  </div>
  <div class="fcol" style="left:634px">
    <h4>QUICK CONTACT</h4>
    <div class="field">NAME</div>
    <div class="field">EMAIL</div>
    <div class="field tall">MESSAGE</div>
    <div class="submit">Submit</div>
  </div>
  <div class="fcol about" style="left:878px">
    <h4>ABOUT BMC</h4>
    <p>Since founding Brightmoor Counsel in 2014 we have dedicated ourselves to the provision of services. What differentiates us from other advisers or consultancies is a genuine motivation to see our clients succeed. Today's technology allows our clients to take their knowledge to the market in ways that previous generations could only.....</p>
  </div>
</footer>

<div class="base">
  <div class="base-brand"><span></span>Brightmoor Counsel</div>
  <div class="copy">Copyrights © 2017 - All Rights Reserved</div>
</div>

</body>
</html>
```